Velmarotix - world unique technology for better life - please let them know who am i at first sight

We need a new business card for company which is a provider of unique crystal based technology suitable for all living being. For more information and final design you can use our brochure (our colours are black and blue from brochure).
We use Verdana font

Industry/Entity Type

Business

Contact Information for Business Card

regular dimension

Font styles to use
Other font styles liked:
• Verdana

Requirements
Must have
• Logo
• name
• function/position
• phone
• mobile
• e-mail
• adress
Nice to have
• inovative design (technology directed)

```html
<!DOCTYPE html>
<html lang="en">
<head>
<meta charset="utf-8">
<title>Velmarotix Business Card</title>
<link rel="stylesheet" href="https://fonts.googleapis.com/css2?family=Questrial&display=swap">
<style>
  :root {
    --brand-blue: #1ba3dd;
    --ink: #2e2e2e;
    --ink-soft: #4a4a4a;
    --swoosh-grey: #a8a8a8;
    --card-light: #ffffff;
    --card-shade: #e4e4e4;
    --backdrop: #eceef0;
    --white: #ffffff;
  }
  * { margin: 0; padding: 0; box-sizing: border-box; }
  html, body { width: 1200px; height: 900px; overflow: hidden; }
  body {
    background: var(--backdrop);
    font-family: "Questrial", sans-serif;
    color: var(--ink);
    position: relative;
  }
  .card {
    position: absolute;
    left: 290px;
    width: 620px;
    height: 355px;
    border-radius: 34px;
    overflow: hidden;
    box-shadow: 0 8px 24px rgba(0,0,0,0.12);
  }
  .card--front {
    top: 62px;
    background: radial-gradient(ellipse at 45% 35%, var(--card-light) 0%, var(--card-shade) 100%);
  }
  .card--back {
    top: 483px;
    background: var(--brand-blue);
  }
  .card__waves { position: absolute; inset: 0; width: 100%; height: 100%; }

  .brand {
    position: absolute;
    display: flex;
    align-items: center;
    gap: 14px;
    left: 50%;
    transform: translateX(-50%);
    white-space: nowrap;
  }
  .brand__dot {
    width: 54px; height: 54px;
    border-radius: 50%;
    background: var(--brand-blue);
  }
  .brand__name {
    font-size: 38px;
    letter-spacing: 1px;
    color: var(--brand-blue);
  }
  .card--front .brand { top: 68px; }
  .card--back .brand { top: 150px; }
  .card--back .brand__dot { background: var(--white); }
  .card--back .brand__name { color: var(--white); }

  .person {
    position: absolute;
    right: 348px;
    top: 180px;
    text-align: right;
    font-variant: small-caps;
    letter-spacing: 1.5px;
  }
  .person__name { font-size: 21px; font-weight: 700; color: var(--ink); }
  .person__role { font-size: 17px; color: var(--ink-soft); margin-top: 2px; }
  .person__address { font-size: 17px; color: var(--ink-soft); margin-top: 16px; line-height: 1.3; }

  .divider {
    position: absolute;
    left: 284px;
    top: 180px;
    width: 1px;
    height: 118px;
    background: var(--ink-soft);
  }

  .contacts {
    position: absolute;
    left: 296px;
    top: 184px;
    list-style: none;
    font-size: 16px;
    letter-spacing: 1.5px;
    color: var(--ink);
  }
  .contacts__item { display: flex; align-items: center; gap: 7px; height: 20px; }
  .contacts__item--gap { margin-top: 8px; }
  .contacts__item--web { font-variant: small-caps; }
  .contacts__icon { width: 13px; height: 13px; flex: none; }
</style>
</head>
<body>

<section class="card card--front" aria-label="Business card front">
  <svg class="card__waves" viewBox="0 0 620 355" preserveAspectRatio="none" aria-hidden="true">
    <path d="M0 262 C 130 250, 300 292, 620 322 L620 355 L0 355 Z" fill="var(--swoosh-grey)"/>
    <path d="M0 280 C 150 272, 320 305, 620 334 L620 355 L0 355 Z" fill="var(--white)"/>
    <path d="M0 288 C 160 282, 330 312, 620 342 L620 355 L0 355 Z" fill="var(--brand-blue)"/>
  </svg>

  <div class="brand">
    <span class="brand__dot"></span>
    <span class="brand__name">VELMAROTIX</span>
  </div>

  <div class="person">
    <p class="person__name">Daniel Reeve</p>
    <p class="person__role">Owner / C.E.O</p>
    <p class="person__address">Suite # 418, Orin Bldg,<br>NY 40917</p>
  </div>

  <div class="divider"></div>

  <ul class="contacts">
    <li class="contacts__item">
      <svg class="contacts__icon" viewBox="0 0 14 14"><circle cx="7" cy="7" r="7" fill="var(--ink)"/><path d="M4.5 3.5 L6 3.5 L6.5 5.5 L5.6 6.2 Q6.5 8 7.8 8.4 L8.5 7.5 L10.5 8 L10.5 9.5 Q7 10.5 4.5 3.5 Z" fill="var(--white)"/></svg>
      555-204-7781
    </li>
    <li class="contacts__item">
      <svg class="contacts__icon" viewBox="0 0 14 14"><circle cx="7" cy="7" r="7" fill="var(--ink)"/><rect x="5" y="3" width="4" height="8" rx="0.8" fill="var(--white)"/></svg>
      555-318-6642
    </li>
    <li class="contacts__item">
      <svg class="contacts__icon" viewBox="0 0 14 14"><circle cx="7" cy="7" r="7" fill="var(--ink)"/><rect x="4" y="5.5" width="6" height="4.5" fill="var(--white)"/><rect x="5" y="3.5" width="4" height="2" fill="var(--white)"/></svg>
      555-472-9915
    </li>
    <li class="contacts__item contacts__item--gap">
      <svg class="contacts__icon" viewBox="0 0 14 14"><circle cx="7" cy="7" r="7" fill="var(--ink)"/><rect x="3.5" y="4.5" width="7" height="5" fill="var(--white)"/><path d="M3.5 4.5 L7 7.5 L10.5 4.5" stroke="var(--ink)" stroke-width="0.8" fill="none"/></svg>
      info@velmarotix-mail.com
    </li>
    <li class="contacts__item contacts__item--web">
      <svg class="contacts__icon" viewBox="0 0 14 14"><circle cx="7" cy="7" r="7" fill="var(--ink)"/><circle cx="7" cy="7" r="4" fill="none" stroke="var(--white)" stroke-width="0.9"/><ellipse cx="7" cy="7" rx="1.8" ry="4" fill="none" stroke="var(--white)" stroke-width="0.8"/><line x1="3" y1="7" x2="11" y2="7" stroke="var(--white)" stroke-width="0.8"/></svg>
      www.velmarotix-web.com
    </li>
  </ul>
</section>

<section class="card card--back" aria-label="Business card back">
  <div class="brand">
    <span class="brand__dot"></span>
    <span class="brand__name">VELMAROTIX</span>
  </div>
</section>

</body>
</html>
```